Heron Dusk business card design

I make handmade colourful women's beaded jewellery (necklaces and earnings).
I require a business card to be designed to truly reflect my jewellery, that is, it is different and stands out.
I would like the business card to look creative, arty, gentle and feminine and fit in with the look of my website and logo (already developed).
I would like the business card to have strong use of the water reeds that are flowing in the wind (please see the banner image on my website www.herondusk.net and attached files).

Target Market(s)

Women who are fashion conscious, hip and funky. My audience like things that are a little different and stand out in a crowd.These women are aged in their 20's-40's.

Industry/Entity Type

Jewelry

Contact Information for Business Card

Please include the following items:
1) my logo: Heron Dusk
2) my name, address and phone number: Darla Fontenot, Sydney, Australia, 0498 315 270
3) my web details: www.herondusk.net, info@herondusk.net, www.facebook.com/herondusk

Font styles to use
Other font styles liked:
• Remachine Script

Requirements
Must have
• My business card must have the following:
• 1) my personal details including all my website contacts (see above).
• 2) Heron Dusk logo
• 3) Reeds flowing in the wind (see my banner image on my website www.herondusk.net or see attached files).
Nice to have
• A sunrise in the background (rising over water)
• I would prefer that the colour scheme to fit with the Heron Dusk logo, that is the colours of an early morning sunrise i.e yellows, oranges. The use of black and white is fine.
Should not have
• I do not like a commercial manufactured look with hard edges. I would like a look that is soft and reflects an artistic, creative and independent business.

```html
<!DOCTYPE html>
<html lang="en">
<head>
<meta charset="utf-8">
<title>Heron Dusk – Business Card</title>
<link rel="stylesheet" href="https://fonts.googleapis.com/css2?family=Arimo:wght@400;700&display=swap">
<style>
  :root {
    --bg: #e9e7e4;
    --card-dark: #2a2627;
    --card-dark-edge: #1c191a;
    --card-light: #ffffff;
    --ink: #2b2b2b;
    --ink-soft: #6b6b6b;
    --sun-light: #ffd84a;
    --sun: #f6b81c;
    --sun-deep: #ee8a12;
    --band: #2d2a2b;
    --rule: #dcdcdc;
  }
  * { margin: 0; padding: 0; box-sizing: border-box; }
  html, body {
    width: 1200px; height: 950px; overflow: hidden;
    background: var(--bg);
    font-family: "Arimo", Arial, sans-serif;
  }
  .stage {
    width: 1200px; height: 950px;
    display: flex; flex-direction: column; align-items: center; justify-content: center;
    gap: 40px;
  }
  .card {
    width: 700px; height: 400px; position: relative; overflow: hidden;
    border-radius: 12px;
    box-shadow: 0 10px 28px rgba(0,0,0,.14);
  }

  /* Shared sunrise emblem */
  .sunrise {
    display: block; border-radius: 50%;
    background:
      radial-gradient(circle at 50% 38%, var(--sun-light) 0%, var(--sun) 45%, transparent 70%),
      linear-gradient(180deg, var(--sun-light) 0%, var(--sun) 50%, var(--sun-deep) 78%, #f29a2e 100%);
  }
  .brand-name { font-weight: 400; letter-spacing: .3px; }

  /* Back side */
  .card--back {
    background: linear-gradient(160deg, #3a3536 0%, var(--card-dark) 55%, var(--card-dark-edge) 100%);
  }
  .back-brand {
    position: absolute; left: 0; right: 0; top: 48px;
    display: flex; flex-direction: column; align-items: center; gap: 10px;
  }
  .back-brand .brand-name { color: #fff; font-size: 30px; }
  .back-brand .sunrise {
    width: 150px; height: 150px;
    box-shadow: 0 0 0 5px #fff, 0 0 30px rgba(246,184,28,.25);
  }
  .back-social { position: absolute; left: 0; right: 0; top: 290px; height: 44px; }
  .back-social svg { display: block; margin: 0 auto; }

  /* Front side */
  .card--front { background: var(--card-light); }
  .front-brand {
    position: absolute; left: 50px; top: 50px; width: 270px;
    display: flex; flex-direction: column; align-items: center; gap: 10px;
  }
  .front-brand .brand-name { color: var(--ink); font-size: 30px; }
  .front-brand .sunrise {
    width: 170px; height: 170px;
    box-shadow: 0 0 0 3px var(--ink);
  }
  .divider {
    position: absolute; left: 350px; top: 40px; width: 1px; height: 220px;
    background: linear-gradient(180deg, transparent, var(--rule) 20%, var(--rule) 80%, transparent);
  }
  .contact {
    position: absolute; left: 380px; top: 56px; color: var(--ink-soft);
    font-size: 15px; line-height: 23px;
  }
  .contact-name { color: var(--ink); font-size: 21px; font-weight: 700; line-height: 26px; }
  .contact-role { color: var(--sun); font-size: 15px; margin-bottom: 10px; }
  .contact-line { display: flex; align-items: center; gap: 9px; }
  .contact-line svg { flex: none; }
  .band-soft {
    position: absolute; left: 0; right: 0; bottom: 74px; height: 20px;
    background: linear-gradient(90deg, rgba(255,255,255,0) 0%, #cfcbca 35%, #6a6566 75%, #3d393a 100%);
  }
  .band {
    position: absolute; left: 0; right: 0; bottom: 0; height: 74px;
    background: linear-gradient(180deg, #353132 0%, var(--band) 100%);
    display: flex; align-items: center; justify-content: center;
  }
  .band-url { color: #fff; font-size: 17px; letter-spacing: 5px; }
  .band-disc {
    position: absolute; right: 28px; bottom: 72px;
    width: 44px; height: 44px;
    box-shadow: 0 0 0 3px #fff;
  }
</style>
</head>
<body>
<main class="stage">

  <section class="card card--back" aria-label="Card back">
    <div class="back-brand">
      <span class="brand-name">Heron Dusk</span>
      <span class="sunrise" role="img" aria-label="Sunrise over water with reeds flowing in the wind"></span>
    </div>
    <div class="back-social">
      <svg width="700" height="44" viewBox="0 0 700 44" aria-hidden="true">
        <defs>
          <linearGradient id="rule-fade" x1="0" x2="1">
            <stop offset="0" stop-color="#fff" stop-opacity="0"/>
            <stop offset=".5" stop-color="#fff" stop-opacity=".55"/>
            <stop offset="1" stop-color="#fff" stop-opacity="0"/>
          </linearGradient>
        </defs>
        <path d="M150 36 Q350 30 550 36" fill="none" stroke="url(#rule-fade)" stroke-width="1"/>
        <circle cx="305" cy="16" r="11" fill="#f6b81c"/>
        <circle cx="335" cy="16" r="11" fill="#f6b81c"/>
        <circle cx="365" cy="16" r="11" fill="#f6b81c"/>
        <circle cx="395" cy="16" r="11" fill="#f6b81c"/>
      </svg>
    </div>
  </section>

  <section class="card card--front" aria-label="Card front">
    <div class="front-brand">
      <span class="brand-name">Heron Dusk</span>
      <span class="sunrise" role="img" aria-label="Sunrise over water with reeds flowing in the wind"></span>
    </div>
    <div class="divider"></div>
    <div class="contact">
      <div class="contact-name">Mara Quill</div>
      <div class="contact-role">President</div>
      <div>Darla Fontenot</div>
      <div>Sydney, Australia</div>
      <div class="contact-line">
        <svg width="14" height="14" viewBox="0 0 14 14" aria-hidden="true"><path d="M3 1l2 3-1.2 1.3a8 8 0 0 0 4.9 4.9L10 9l3 2-1 2.5C6 13 1 8 .5 2z" fill="#2b2b2b"/></svg>
        <span>0498 315 270</span>
      </div>
      <div class="contact-line">
        <svg width="14" height="14" viewBox="0 0 14 14" aria-hidden="true"><rect x="1" y="3" width="12" height="8" rx="1.5" fill="none" stroke="#2b2b2b" stroke-width="1.5"/><path d="M1 3l6 5 6-5" fill="none" stroke="#2b2b2b" stroke-width="1.5"/></svg>
        <span>info@herondusk.net</span>
      </div>
      <div class="contact-line">
        <svg width="14" height="14" viewBox="0 0 14 14" aria-hidden="true"><rect x="1" y="1" width="12" height="12" rx="2" fill="#2b2b2b"/></svg>
        <span>herondusk</span>
      </div>
    </div>
    <div class="band-soft"></div>
    <span class="sunrise band-disc" role="img" aria-label="Small sunrise emblem"></span>
    <div class="band"><span class="band-url">www.herondusk.net</span></div>
  </section>

</main>
</body>
</html>
```